Maple Roster Business Card for recruitment company

We are looking for a Business Card Design that incorporates our personal details and our busines name and logo. We are a specialized search consultancy that recruit Property and Construction professionals.
We would like a business card that stands out and is appealing to the Construction and Property industry as well.

Target Market(s)

people in the construction and property industry

Contact Information for Business Card

Business Name and logo

Font styles to use
Serif

Colors
0094D4
00A9DD
6FCCEA
C7EBF8
E9F6FB

Requirements
Must have
• Business name and logo as well as contact details
Should not have
• No photos of us please

```html
<!DOCTYPE html>
<html lang="en">
<head>
<meta charset="utf-8">
<title>Maple Roster – Business Card</title>
<link rel="stylesheet" href="https://fonts.googleapis.com/css2?family=Questrial&family=Mulish:wght@800&display=swap">
<style>
  :root {
    --stage: #2b2c2d;
    --card-front: #f7f7f7;
    --card-front-shade: #ececec;
    --navy: #073a4f;
    --navy-deep: #052b3b;
    --ink: #333b40;
    --white: #ffffff;
  }
  * { margin: 0; padding: 0; box-sizing: border-box; }
  html, body { width: 1200px; height: 732px; overflow: hidden; }
  body {
    background: var(--stage);
    position: relative;
    font-family: "Questrial", sans-serif;
  }
  .card {
    position: absolute;
    top: 242px;
    width: 436px;
    height: 248px;
    overflow: hidden;
  }
  .card--front {
    left: 144px;
    background: linear-gradient(160deg, var(--white) 0%, var(--card-front) 50%, var(--card-front-shade) 100%);
  }
  .card--back {
    left: 621px;
    background: linear-gradient(135deg, var(--navy) 0%, #0a3d52 45%, var(--navy-deep) 100%);
  }
  .wordmark {
    position: absolute;
    display: flex;
    align-items: center;
    gap: 8px;
    font-family: "Questrial", sans-serif;
    font-weight: 400;
    letter-spacing: 0.02em;
    white-space: nowrap;
  }
  .wordmark__dot {
    display: block;
    border-radius: 50%;
    background: currentColor;
  }
  .card--front .wordmark {
    right: 59px;
    top: 73px;
    font-size: 27px;
    color: var(--navy);
  }
  .card--front .wordmark__dot { width: 10px; height: 10px; }
  .card--back .wordmark {
    left: 97px;
    top: 108px;
    font-size: 36px;
    color: var(--white);
  }
  .card--back .wordmark__dot { width: 12px; height: 12px; }
  .contact {
    position: absolute;
    right: 59px;
    top: 136px;
    text-align: right;
    color: var(--ink);
  }
  .contact__name {
    font-family: "Mulish", sans-serif;
    font-weight: 800;
    font-size: 17px;
    color: var(--navy);
    line-height: 20px;
  }
  .contact__role {
    font-size: 13px;
    line-height: 16px;
    letter-spacing: 0.02em;
  }
  .contact__lines {
    margin-top: 13px;
    list-style: none;
    font-size: 12.5px;
    line-height: 14.3px;
    letter-spacing: 0.01em;
  }
  .contact__label {
    font-family: "Mulish", sans-serif;
    font-weight: 800;
    color: var(--navy);
    margin-right: 10px;
  }
</style>
</head>
<body>
  <section class="card card--front" aria-label="Business card front">
    <div class="wordmark"><span>MAPLE ROSTER</span><span class="wordmark__dot"></span></div>
    <div class="contact">
      <p class="contact__name">Clara Whitfield</p>
      <p class="contact__role">Director | Senior Search Consultant</p>
      <ul class="contact__lines">
        <li><span class="contact__label">T:</span>+64 21 480 2290</li>
        <li><span class="contact__label">E:</span>clara@mapleroster.nz</li>
        <li><span class="contact__label">W:</span>www.mapleroster.nz</li>
      </ul>
    </div>
  </section>

  <section class="card card--back" aria-label="Business card back">
    <div class="wordmark"><span>MAPLE ROSTER</span><span class="wordmark__dot"></span></div>
  </section>
</body>
</html>
```